Harbor Crestline (Business Card Design)

Need business cards designed. Something modern, chic, and sleek. Mabye the back of the card should be the navy blue that is in the logo and then just the logo on the back.

Target Market(s)

Those in the hotel, office, and renovation industry

Contact Information for Business Card

1. Logo 2. Dorian Fenwick 3. CEO/Founder 4. Phone: (833) HarbCre / (833) 427-2731 5. Email: dorian@theharborcrestline.com 6. Website: www.theharborcrestline.com

Font styles to use
Other font styles liked:
• Look at the logo font and base the font for everything else off of that.

Colors
0054AA
0677BA
7BADD7
CADEEF
E8F1F8

Requirements
Must have
• Colors that are associated in the logo
Nice to have
• Sleek modern clean and chic design.

```html
<!DOCTYPE html>
<html lang="en">
<head>
<meta charset="utf-8">
<title>Harbor Crestline — Business Card</title>
<link rel="stylesheet" href="https://fonts.googleapis.com/css2?family=Montserrat:wght@400;500;600;800&display=swap">
<style>
  :root {
    --navy: #0c1a45;
    --gold: #cfa448;
    --white: #ffffff;
    --ink: #1d1d1f;
    --backdrop: #262626;
  }
  * { box-sizing: border-box; margin: 0; padding: 0; }
  html, body { width: 1200px; height: 875px; overflow: hidden; }
  body {
    background: var(--backdrop);
    font-family: "Montserrat", sans-serif;
    position: relative;
  }
  .card {
    position: absolute;
    width: 560px;
    height: 320px;
    border-radius: 22px;
    overflow: hidden;
    box-shadow: 0 18px 40px rgba(0,0,0,0.45);
  }
  /* Front */
  .card-front { left: 60px; top: 90px; background: var(--white); }
  .front-brand {
    position: absolute;
    left: 34px; bottom: 40px;
    display: flex; align-items: center; gap: 12px;
  }
  .brand-square { width: 22px; height: 22px; background: var(--gold); flex: none; }
  .front-brand .brand-name {
    font-weight: 800;
    font-size: 26px;
    color: var(--navy);
    letter-spacing: 0.5px;
  }
  .front-details {
    position: absolute;
    right: 34px; top: 44px;
    text-align: right;
  }
  .person-name {
    font-weight: 800;
    font-size: 34px;
    color: var(--navy);
    line-height: 1;
  }
  .person-title {
    font-weight: 600;
    font-size: 16px;
    color: var(--gold);
    margin-top: 6px;
  }
  .rule {
    width: 40px; height: 2px;
    background: var(--navy);
    margin: 12px 0 14px auto;
  }
  .contact-list { list-style: none; }
  .contact-list li {
    display: flex; justify-content: flex-end; align-items: center; gap: 8px;
    font-weight: 400;
    font-size: 14px;
    color: var(--ink);
    line-height: 1.55;
  }
  .contact-list svg { width: 12px; height: 12px; flex: none; }
  /* Back */
  .card-back {
    left: 580px; top: 465px;
    background: var(--navy);
    display: flex; align-items: center; justify-content: center; gap: 16px;
  }
  .card-back .brand-name {
    font-weight: 500;
    font-size: 30px;
    letter-spacing: 5px;
    text-transform: uppercase;
    color: var(--white);
  }
</style>
</head>
<body>
  <section class="card card-front" aria-label="Business card front">
    <div class="front-brand">
      <span class="brand-square"></span>
      <span class="brand-name">Harbor Crestline</span>
    </div>
    <div class="front-details">
      <h1 class="person-name">Dorian Fenwick</h1>
      <p class="person-title">CEO/Founder</p>
      <div class="rule"></div>
      <ul class="contact-list">
        <li>(833) HarbCre
          <svg viewBox="0 0 24 24" fill="var(--gold)"><path d="M6.6 10.8a15.1 15.1 0 0 0 6.6 6.6l2.2-2.2a1 1 0 0 1 1-.25 11.4 11.4 0 0 0 3.6.57 1 1 0 0 1 1 1V20a1 1 0 0 1-1 1A17 17 0 0 1 3 4a1 1 0 0 1 1-1h3.5a1 1 0 0 1 1 1c0 1.25.2 2.45.57 3.57a1 1 0 0 1-.25 1z"/></svg>
        </li>
        <li>(833) 427-2731
          <svg viewBox="0 0 24 24" fill="var(--gold)"><path d="M6.6 10.8a15.1 15.1 0 0 0 6.6 6.6l2.2-2.2a1 1 0 0 1 1-.25 11.4 11.4 0 0 0 3.6.57 1 1 0 0 1 1 1V20a1 1 0 0 1-1 1A17 17 0 0 1 3 4a1 1 0 0 1 1-1h3.5a1 1 0 0 1 1 1c0 1.25.2 2.45.57 3.57a1 1 0 0 1-.25 1z"/></svg>
        </li>
        <li>dorian@theharborcrestline.com
          <svg viewBox="0 0 24 24" fill="var(--gold)"><path d="M2 5h20v14H2z"/><path d="M2 5l10 8 10-8" fill="none" stroke="var(--white)" stroke-width="2"/></svg>
        </li>
        <li>www.theharborcrestline.com
          <svg viewBox="0 0 24 24" fill="none" stroke="var(--gold)" stroke-width="2.4"><circle cx="12" cy="12" r="9.5"/><path d="M2.5 12h19M12 2.5c3 3 3 16 0 19M12 2.5c-3 3-3 16 0 19"/></svg>
        </li>
      </ul>
    </div>
  </section>

  <section class="card card-back" aria-label="Business card back">
    <span class="brand-square"></span>
    <span class="brand-name">Harbor Crestline</span>
  </section>
</body>
</html>
```